Church Website with Home Page and Member Sermon Library

I am in need of an updated design for our church website. This will include 4 pages (outlined below). We are a conservative, evangelical, Christian church. The site should be modern and clean, while still reflecting our conservative values. I already have a logo for our church, and I want the site to incorporate the logo, and match the logo/branding. Stock photos are allowed if needed, but I have uploaded some images of our church and would prefer those images to be used if possible. Any stock photos used should not include any people in the photos (scenery, nature, buildings, animals, etc. are fine).

The site will need 4 pages: Home, Support Us (Donate), Login, and Recording Library.

Page 1: Home
The home page should include the following sections:

- Navigation: Should include links to each section of the home page plus a "listen live" link which will take the user to a live-streaming site and a "support us" link which will take the user to a support/donate page.

- Announcements: Can be either a banner or some other design, but there needs to be some way for us to post announcements for visitors to see. I'm open for creative ideas in this section, but would like it not to take up a lot of room on the page.

- About Us: Should include address, service times (see attached document), and information about the church.

- Pastor Bio: A section that introduces our pastor and gives a short bio about our pastor. Would like this section to include a picture of our pastor. Somewhere in this section I would like to include this Bible reference: "And I will give you pastors according to mine heart, which shall feed you with knowledge and understanding. Jer 3:15 LPW"

- Articles of Faith (What We Believe): This should include several sub-sections each with a heading, body, and possibly 1 or more scripture references. I have attached a document to the brief that includes our articles of faith. Feel free to be creative with this section in how you lay these out and format them.

- Support Us: A small section that explains what kind of support someone can give and a link to a donation page. The link can say something like "Support Us" or "Donate Now".

- Contact form: A contact form that allows the visitor to send us a message. The contact form should ask for name, email, phone, and message.

- Footer: A footer that will be displayed on all pages of the site. This should include at a minimum a link to the home page (or a link to each individual section in the home page if you prefer), a link to "listen live", a link to "support us", a link to "contact us" (or you can put the contact form directly in the footer if you prefer), the address, and a "member login" link.

Page 2: Support Us
The donation page should include a form the visitor can fill out to make a donation. We will embed a third party form later. For this design, please just mock out the design with a basic form asking for name, phone, and email.

Page 3: Login
The recording library (detailed below) will require members to login with a shared numeric code before accessing the page. We need a design for a login screen. The screen should include navigation/footer just like all other pages, but the body of the login page will consist only of a form that asks the user to enter the access code and then a "login" button.

Page 4: Recording Library

The library page is a member-only page that will require a shared, numeric pass code to access. On this page, members will be able to access a filterable list of past sermons. The page by default should display most recent sermons, but should also include a search form that allows the member to filter the sermon list to find a particular sermon. The search form should allow the user to select a filter type (e.g. Speaker name, date, event, etc.) and type in a value to search. They should be able to add multiple filters and remove filters that have been added. Each sermon that is displayed in the result list should include basic information such as title, date, speaker, tags, etc. along with a download icon, and an embedded audio player where they can click a play button to stream it on-demand. Each sermon should also have clickable tags associated with it that can be used to find related sermons.
Updates

I have uploaded several images of our church. Feel free to incorporate these into your design if possible.

Target Market(s)

Church Members

Industry/Entity Type

Religion

Number of Pages Required

4 page

Font styles to use
Sans Serif

Colors

Designer to choose colors to be used in the design.

Requirements
Must have
• Must incorporate the logo (attached)
Nice to have
• Would like the design to incorporate pictures of our church (attached) instead of stock photos if possible.
Should not have
• Please avoid an overly cluttered design. Stock photos used should not include any people in the photos.

```html
<!DOCTYPE html>
<html lang="en">
<head>
<meta charset="utf-8">
<title>Donation – Cedar Grace Church</title>
<link href="https://fonts.googleapis.com/css2?family=Cinzel:wght@400&family=Cormorant+Garamond:wght@500&family=Cormorant+SC:wght@500&family=Montserrat:wght@400;500;700&family=Poppins:wght@400;600&display=swap" rel="stylesheet">
<style>
:root{
  --green:#82a86d;
  --ink:#1d1d1d;
  --muted:#6b6b6b;
  --line:#dcdcdc;
  --navy:#1c2541;
  --footer:#2e2e2e;
  --footer-text:#cfcfcf;
  --white:#ffffff;
}
*{box-sizing:border-box;margin:0;padding:0}
html,body{width:722px;height:1200px;overflow:hidden;background:var(--white)}
body{position:relative;font-family:"Montserrat",sans-serif;color:var(--ink)}
/* hero */
.hero{position:absolute;left:0;top:0;width:722px;height:273px;
  background:linear-gradient(180deg,#ffffff 0%,rgba(255,255,255,.6) 14%,rgba(255,255,255,0) 30%),
  linear-gradient(180deg,#efe9df 0%,#ece3d4 45%,#d9b88c 72%,#b88554 100%);}
.hero-shade{position:absolute;inset:0;background:radial-gradient(ellipse at 50% 45%,rgba(255,255,255,.55),rgba(255,255,255,0) 60%)}
.church-name{position:absolute;text-align:center;font-family:"Montserrat",sans-serif;font-weight:500;color:var(--green);line-height:1.25}
.nav{position:absolute;top:33px;left:315px;display:flex;gap:21px;font-family:"Poppins",sans-serif;font-size:8.5px;color:#333;line-height:12px}
.btn{position:absolute;background:var(--green);color:var(--white);font-family:"Cormorant Garamond",serif;font-weight:500;font-size:10px;letter-spacing:.3px;display:flex;align-items:center;justify-content:center}
.hero-title{position:absolute;top:140px;left:0;width:722px;text-align:center;font-family:"Cormorant SC",serif;font-weight:500;font-size:38px;letter-spacing:4px;color:#111;line-height:44px}
.rule{position:absolute;background:#111}
/* form */
.intro{position:absolute;left:161px;top:326px;font-size:9px}
.panel{position:absolute;left:161px;width:399px;border:1px solid var(--line)}
.heading{position:absolute;font-size:8.5px;letter-spacing:1.1px;font-weight:500}
.label{position:absolute;font-size:8.5px;letter-spacing:.8px;color:var(--muted)}
.field{position:absolute;border:1px solid var(--line);height:26px;background:var(--white)}
.amount{position:absolute;top:380px;width:115px;height:26px;border:1px solid var(--line);display:flex;align-items:center;justify-content:center;font-size:9px;color:#555;letter-spacing:.5px}
.amount.active{background:var(--green);border-color:var(--green);color:var(--white);font-weight:700}
.placeholder{position:absolute;font-size:8.5px;color:#b0b0b0;letter-spacing:.5px}
.radio{position:absolute;width:10px;height:10px;border-radius:50%;border:1px solid #555}
.radio.on{border-color:var(--green)}
.radio.on::after{content:"";position:absolute;left:2px;top:2px;width:4px;height:4px;border-radius:50%;background:var(--green)}
.method{position:absolute;font-family:"Poppins",sans-serif;font-weight:600;font-size:8.5px;color:var(--navy)}
.method-note{position:absolute;font-family:"Poppins",sans-serif;font-size:7px;line-height:12px;color:#444}
.card{position:absolute;top:870px;width:22px;height:15px;border-radius:2px}
/* footer */
.footer{position:absolute;left:0;top:1006px;width:722px;height:194px;background:var(--footer)}
.f-head{position:absolute;top:1054px;font-family:"Cinzel",serif;font-size:12px;letter-spacing:1.5px;color:var(--white)}
.f-text{position:absolute;font-family:"Poppins",sans-serif;font-size:7px;line-height:9px;color:var(--footer-text)}
.f-icon{position:absolute;width:7px;height:7px}
.divider{position:absolute;left:0;top:1163px;width:722px;height:1px;background:#3f3f3f}
.social{position:absolute;top:1177px;width:6px;height:6px;border-radius:50%;background:var(--white)}
</style>
</head>
<body>

<header>
  <div class="hero" role="img" aria-label="Church sanctuary interior with wooden pews and a pulpit, softly lit"><div class="hero-shade"></div></div>
  <div class="church-name" style="left:96px;top:46px;width:100px;font-size:11px">Cedar Grace<br>Church</div>
  <nav class="nav"><span>Home</span><span>About</span><span>Our Pastor</span><span>Articles Of Faith</span></nav>
  <div class="btn" style="left:557px;top:28px;width:59px;height:22px">DONATE</div>
  <h1 class="hero-title">DONATION</h1>
  <div class="rule" style="left:312px;top:190px;width:97px;height:1.5px"></div>
  <div class="rule" style="left:337px;top:194px;width:47px;height:.5px"></div>
</header>

<main>
  <p class="intro">Registered before? Log in to use your saved details.</p>

  <section class="panel" style="top:349px;height:126px"></section>
  <div class="heading" style="left:182px;top:364px">YOUR DONATION</div>
  <div class="amount" style="left:183px">$20,00</div>
  <div class="amount active" style="left:303px">$50,00</div>
  <div class="amount" style="left:423px">$100,00</div>
  <div class="heading" style="left:182px;top:418px">CUSTOM AMOUNT</div>
  <div class="field" style="left:183px;top:434px;width:355px"></div>
  <div class="placeholder" style="left:193px;top:443px">$0,00</div>

  <section class="panel" style="top:486px;height:247px"></section>
  <div class="heading" style="left:183px;top:501px">DETAILS</div>
  <div class="label" style="left:183px;top:523px">First name *</div>
  <div class="label" style="left:365px;top:523px">Last name *</div>
  <div class="field" style="left:183px;top:536px;width:172px"></div>
  <div class="field" style="left:365px;top:536px;width:173px"></div>
  <div class="label" style="left:183px;top:574px">Email *</div>
  <div class="label" style="left:365px;top:574px">Phone</div>
  <div class="field" style="left:183px;top:588px;width:172px"></div>
  <div class="field" style="left:365px;top:588px;width:173px"></div>
  <div class="label" style="left:183px;top:626px">Address</div>
  <div class="field" style="left:183px;top:639px;width:355px"></div>
  <div class="label" style="left:183px;top:677px">City</div>
  <div class="label" style="left:365px;top:677px">Postcode</div>
  <div class="field" style="left:183px;top:691px;width:172px"></div>
  <div class="field" style="left:365px;top:691px;width:173px"></div>

  <section class="panel" style="top:744px;height:162px"></section>
  <div class="heading" style="left:183px;top:759px">CHOOSE YOUR PAYMENT METHOD</div>
  <div class="radio" style="left:184px;top:786px"></div>
  <div class="method" style="left:201px;top:785px">QuickPay</div>
  <div class="method-note" style="left:201px;top:801px">You’ll be forwarded to QuickPay to complete<br>your payment.</div>
  <div class="radio on" style="left:184px;top:850px"></div>
  <div class="method" style="left:201px;top:849px">Credit / Debit Card</div>
  <div class="card" style="left:203px;background:#1a5bb5"></div>
  <div class="card" style="left:228px;background:#2a2f66"></div>

  <div class="btn" style="left:161px;top:926px;width:59px;height:22px">DONATE</div>
</main>

<footer>
  <div class="footer"></div>
  <div class="church-name" style="left:107px;top:1098px;width:120px;font-size:13px">Cedar Grace<br>Church</div>

  <div class="f-head" style="left:297px">CONTACT</div>
  <svg class="f-icon" style="left:298px;top:1083px" viewBox="0 0 10 10"><path d="M5 9.5S1.8 6 1.8 4a3.2 3.2 0 0 1 6.4 0C8.2 6 5 9.5 5 9.5z" fill="none" stroke="#cfcfcf" stroke-width="1"/><circle cx="5" cy="4" r="1.1" fill="none" stroke="#cfcfcf" stroke-width=".9"/></svg>
  <div class="f-text" style="left:308px;top:1082px">418 Millbrook Ln. Fairview,<br>Ohio 45302</div>
  <svg class="f-icon" style="left:298px;top:1108px" viewBox="0 0 10 10"><path d="M2.2 1.2l1.6 1.9-.9 1.2c.6 1.2 1.5 2.1 2.7 2.7l1.2-.9 1.9 1.6-.9 1.1C4.4 8.6 1.4 5.6 1.1 2.1z" fill="none" stroke="#cfcfcf" stroke-width=".9"/></svg>
  <div class="f-text" style="left:308px;top:1107px">+1 555 204 118 37</div>
  <svg class="f-icon" style="left:298px;top:1123px" viewBox="0 0 10 10"><rect x="1" y="2.2" width="8" height="5.6" fill="none" stroke="#cfcfcf" stroke-width=".9"/><path d="M1 2.4l4 3 4-3" fill="none" stroke="#cfcfcf" stroke-width=".9"/></svg>
  <div class="f-text" style="left:308px;top:1122px;letter-spacing:.4px">cedargracechurch@mail.org</div>

  <div class="f-head" style="left:474px">DONATION</div>
  <div class="f-text" style="left:474px;top:1079px;line-height:11px">Aliquam at commodo venenatis quis.<br>Velit neque interdum molestie risus.</div>
  <div class="btn" style="left:474px;top:1110px;width:59px;height:22px">DONATE</div>

  <div class="divider"></div>
  <div class="f-text" style="left:107px;top:1176px;color:var(--white)">Copyright 2023 Cedar Grace Church I All rights reserved</div>
  <div class="social" style="left:552px"></div>
  <div class="social" style="left:568px"></div>
  <div class="social" style="left:584px"></div>
  <div class="social" style="left:601px"></div>
</footer>

</body>
</html>
```